Business Card for premium dental clinic

We are a premium dental clinic based in Brasov, Romania with more than 15 year on the market, providing quality dental treatment made by a team of more specialized dentists, working with modern equipment as a solution to beautiful and healthy teeth.

Our current logo for the clinic use 2 square with colors black and gold - dr Ternisu - studio, using family fonts Bodoni, Myriad Pro and Segoe Print.
Depending on the printing we used some gold CMYK background or gold foil picture background or a gold gradient.
We want a business card:
- eye catching business card
- distinguished business card
- premium design
- to keep the color scheme of black and gold
- to attract the customers to spent time reading the information
- modern concept

```html
<!DOCTYPE html>
<html lang="en">
<head>
<meta charset="UTF-8">
<title>Ternisu Dental Clinic – business card</title>
<link rel="stylesheet" href="https://fonts.googleapis.com/css2?family=Montserrat:wght@400;500&family=Oswald:wght@600&display=swap">
<style>
  :root {
    --stage: #1c1c1c;
    --card: #1a1a1a;
    --card-edge: #262626;
    --gold: #f2c230;
    --ink-light: #f2f2f2;
  }
  * { margin: 0; padding: 0; box-sizing: border-box; }
  html, body {
    width: 1200px; height: 900px; overflow: hidden;
    background: var(--stage);
  }
  .canvas {
    position: relative; width: 1200px; height: 900px;
    display: flex; flex-direction: column; align-items: center; justify-content: center;
    gap: 36px;
  }
  .card {
    position: relative; width: 640px; height: 366px;
    background: linear-gradient(135deg, var(--card) 0%, #202020 60%, var(--card-edge) 100%);
    box-shadow: 0 12px 30px rgba(0,0,0,.55);
  }
  /* front */
  .card--front { display: flex; align-items: center; justify-content: center; }
  .brand-name {
    font-family: "Montserrat", sans-serif; font-weight: 500;
    font-size: 26px; letter-spacing: 3px; text-transform: uppercase;
    color: var(--gold);
  }
  /* back */
  .card--back { font-family: "Montserrat", sans-serif; color: var(--ink-light); }
  .identity {
    position: absolute; top: 118px; left: 120px;
    display: flex; align-items: center;
  }
  .identity__name {
    font-family: "Oswald", sans-serif; font-weight: 600;
    font-size: 42px; letter-spacing: 2px; color: var(--gold);
  }
  .identity__rule { width: 2px; height: 70px; background: var(--gold); margin: 0 34px; }
  .contacts { list-style: none; display: flex; flex-direction: column; gap: 4px; }
  .contacts__item { display: flex; align-items: center; gap: 10px; font-size: 18px; letter-spacing: .8px; }
  .contacts__icon { width: 14px; height: 14px; flex: none; }
  .address {
    position: absolute; left: 0; right: 0; bottom: 44px;
    text-align: center; font-size: 18px; letter-spacing: 1px;
  }
</style>
</head>
<body>
<main class="canvas">
  <section class="card card--front" aria-label="Card front">
    <p class="brand-name">Ternisu Dental Clinic</p>
  </section>

  <section class="card card--back" aria-label="Card back">
    <div class="identity">
      <h1 class="identity__name">DR TERNISU</h1>
      <span class="identity__rule"></span>
      <ul class="contacts">
        <li class="contacts__item">
          <svg class="contacts__icon" viewBox="0 0 24 24" fill="none" stroke="#f2c230" stroke-width="2.2"><path d="M5 3h4l2 5-2.5 1.5a11 11 0 0 0 6 6L16 13l5 2v4a2 2 0 0 1-2 2A17 17 0 0 1 3 5a2 2 0 0 1 2-2z"/></svg>
          +40 268 555 019
        </li>
        <li class="contacts__item">
          <svg class="contacts__icon" viewBox="0 0 24 24" fill="none" stroke="#f2c230" stroke-width="2.2"><rect x="3" y="5" width="18" height="14"/><path d="M3 6l9 7 9-7"/></svg>
          info@drternisu.ro
        </li>
        <li class="contacts__item">
          <svg class="contacts__icon" viewBox="0 0 24 24" fill="none" stroke="#f2c230" stroke-width="2"><circle cx="12" cy="12" r="9"/><path d="M3 12h18M12 3c3 3 3 15 0 18M12 3c-3 3-3 15 0 18"/></svg>
          www.drternisu.ro
        </li>
      </ul>
    </div>
    <p class="address">Strada Lungă 42, Brașov 500035, Romania</p>
  </section>
</main>
</body>
</html>
```